CBD/HEMP website for e-commerce store

I need a CBD website for my shopify store. I am looking for a layout similar to these site ( https://quietmeadowcbd.com/ ) (https://elmridgecbd.com/) but with my logo and products. I am attaching what my logo looks like so that it helps with the design.

Target Market(s)

CBD HEMP CANNABIS

Industry/Entity Type

Cannabis

Coding

Coded - Design and coding required

Number of Pages Required

5+ page

Requirements
Nice to have
• I would like for it to have a trendy/galaxy feel

```html
<!DOCTYPE html>
<html lang="en">
<head>
<meta charset="utf-8">
<title>Starleaf — Hemp &amp; CBD Store</title>
<link rel="stylesheet" href="https://fonts.googleapis.com/css2?family=Lato:wght@400;700;900&family=Playfair+Display:wght@700&family=Cormorant+Garamond:wght@500&display=swap">
<style>
:root{
  --pink:#ec2a8d;
  --navy:#0c0d22;
  --ink:#1e1e1e;
  --muted:#666;
  --grey-band:#f2f2f2;
  --tile:#e4e4e4;
  --white:#fff;
  --line:#dcdcdc;
}
*{box-sizing:border-box;margin:0;padding:0}
html,body{width:1200px;height:3784px;overflow:hidden}
body{font-family:"Lato",sans-serif;color:var(--ink);background:var(--white);position:relative}
section,header,footer,nav{position:relative;width:1200px;overflow:hidden}
.abs{position:absolute}
.serif-title{font-family:"Cormorant Garamond",serif;font-weight:500;font-size:40px;letter-spacing:1px;text-align:center;text-transform:uppercase}
.lead{font-size:15px;text-align:center;color:#333}
.icon{fill:none;stroke:currentColor;stroke-width:1.6;stroke-linecap:round;stroke-linejoin:round}

/* top bar */
.topbar{height:43px;background:var(--navy);color:var(--white);font-size:11px}
.topbar .item{top:0;height:43px;display:flex;align-items:center;gap:7px}
/* header */
.masthead{height:86px;background:radial-gradient(ellipse at 50% 50%,#3a1b5e 0%,#16123a 35%,#0a0a1e 80%)}
.brand{font-weight:900;font-size:30px;color:var(--white);letter-spacing:3px;display:flex;align-items:center;gap:10px}
.brand .dot{width:16px;height:16px;border-radius:50%;background:var(--pink)}
/* nav */
.mainnav{height:59px;background:var(--white);border-bottom:1px solid #eee}
.mainnav .link{top:20px;font-size:15px;font-weight:700;letter-spacing:.3px;transform:translateX(-50%);color:#222}
.mainnav .link.active{color:var(--pink);font-weight:400}
/* hero */
.hero{height:605px;background:radial-gradient(ellipse at 75% 30%,#6a2a7a 0%,transparent 45%),radial-gradient(ellipse at 20% 70%,#2a3d8c 0%,transparent 50%),linear-gradient(160deg,#1b1d52,#30277a 45%,#141640)}
.hero h1{top:190px;width:100%;text-align:center;font-family:"Playfair Display",serif;font-size:64px;color:var(--white);letter-spacing:1px}
.hero p{top:272px;width:100%;text-align:center;color:var(--white);font-size:18px;line-height:29px}
.btn-ghost{border:2px solid var(--white);color:var(--white);font-size:16px;display:flex;align-items:center;justify-content:center}
.dots{display:flex;gap:7px}
.dots span{width:12px;height:12px;border-radius:50%;background:#9a9ab0}
.dots span.on{background:var(--white)}
/* products */
.products{height:683px}
.card{width:232px;top:177px}
.card .shot{height:255px;background:var(--tile);position:relative}
.pouch{position:absolute;left:66px;top:48px;width:100px;height:150px;border-radius:8px 8px 4px 4px}
.card .btn-cart{margin:14px auto 0;width:173px;height:40px;border:2px solid #555;display:flex;align-items:center;justify-content:center;font-size:16px;color:#333}
.card .name{text-align:center;font-size:15px;margin-top:14px}
.card .price{text-align:center;font-size:18px;font-weight:700;margin-top:6px}
.pager span{width:11px;height:11px;border-radius:50%;background:#c8c8c8}
.pager span.on{background:var(--pink)}
/* categories */
.categories{height:548px;background:var(--grey-band)}
.cat{top:93px;width:374px;height:420px}
.cat .label{position:absolute;top:321px;width:100%;text-align:center;color:var(--white);font-weight:900;font-size:32px}
.cat .shop{position:absolute;top:362px;left:50%;transform:translateX(-50%);width:142px;height:40px;background:var(--pink);color:var(--white);font-weight:700;font-size:16px;display:flex;align-items:center;justify-content:center}
/* story band */
.story{height:482px;background:radial-gradient(ellipse at 62% 25%,#4a5a22 0%,transparent 35%),radial-gradient(ellipse at 30% 80%,#2b3514 0%,transparent 45%),linear-gradient(180deg,#161a0c,#0d1008)}
.story h2{top:148px;width:100%;text-align:center;font-weight:900;font-size:54px;color:var(--white)}
.story p{top:226px;left:260px;width:680px;text-align:center;color:var(--white);font-size:16.5px;line-height:30px}
/* blog */
.blog{height:652px}
.post{top:176px;width:314px;height:400px;border:1px solid #e2e2e2}
.post .shot{height:203px}
.meta{display:flex;gap:18px;font-size:11px;color:#333;padding:16px 12px 0;align-items:center}
.meta span{display:flex;gap:5px;align-items:center}
.post h3{font-size:17px;font-weight:700;padding:11px 10px 0}
.post p{font-size:12px;line-height:26px;color:var(--muted);padding:6px 10px 0}
.post .more{font-size:12px;font-weight:900;color:var(--pink);padding:4px 10px 0;display:flex;gap:5px;align-items:center}
/* newsletter */
.newsletter{height:323px;background:linear-gradient(180deg,#22305a 0%,#2d3b62 55%,#1a2038 80%,#0c0f1c 100%)}
.newsletter .serif-title{color:var(--white);top:88px;width:100%;font-size:37px}
.newsletter .sub{top:145px;width:100%;text-align:center;color:var(--white);font-size:16px}
.field{left:304px;top:190px;width:589px;height:52px;background:var(--white);display:flex;align-items:center;padding-left:26px;font-size:14px;color:#555}
.send{left:834px;top:190px;width:59px;height:52px;background:var(--pink);display:flex;align-items:center;justify-content:center}
/* footer */
.footer{height:303px;background:radial-gradient(ellipse at 15% 30%,#3c1e5e 0%,transparent 30%),linear-gradient(180deg,#12122e,#0a0a1c);color:var(--white)}
.footer h4{font-size:14px;font-weight:700;letter-spacing:.3px;margin-bottom:12px}
.footer li{list-style:none;font-size:13px;line-height:23.5px;display:flex;gap:8px;align-items:center}
.social{width:44px;height:44px;border:2px solid var(--white);border-radius:50%}
.copyright{top:268px;width:100%;text-align:center;font-size:13px}
</style>
</head>
<body>

<header class="topbar">
  <div class="abs item" style="left:112px">
    <svg width="14" height="18" viewBox="0 0 14 18"><path d="M7 1a6 6 0 0 0-6 6c0 4.5 6 10 6 10s6-5.5 6-10a6 6 0 0 0-6-6z" fill="#fff"/><circle cx="7" cy="7" r="2.2" fill="#0c0d22"/></svg>
    <span>123 LOREM SED XY 0000</span>
  </div>
  <div class="abs item" style="left:482px">
    <svg width="26" height="18" viewBox="0 0 26 18" class="icon" style="color:#fff"><rect x="1" y="2" width="15" height="11"/><path d="M16 6h5l4 4v3h-9z"/><circle cx="6" cy="15" r="2"/><circle cx="20" cy="15" r="2"/></svg>
    <span>FREE SHIPPING ON ORDERS OVER $50!</span>
  </div>
  <div class="abs item" style="right:110px;font-weight:700;font-size:12px">COME BACK DAILY ! !</div>
</header>

<header class="masthead">
  <div class="abs" style="left:113px;top:32px;display:flex;align-items:center;gap:10px;color:#fff;font-size:12px">
    <svg width="44" height="22" viewBox="0 0 44 22" role="img" aria-label="English language flag"><rect width="44" height="22" fill="#1f3a8a"/><path d="M0 0L44 22M44 0L0 22" stroke="#fff" stroke-width="4"/><path d="M22 0v22M0 11h44" stroke="#fff" stroke-width="6"/><path d="M22 0v22M0 11h44" stroke="#c8102e" stroke-width="3"/></svg>
    <span>EN</span>
  </div>
  <div class="abs brand" style="left:50%;top:24px;transform:translateX(-50%)"><span class="dot"></span>STARLEAF</div>
  <div class="abs" style="right:110px;top:33px;display:flex;align-items:center;gap:8px;color:#fff;font-size:14px">
    <svg width="20" height="20" viewBox="0 0 20 20" class="icon"><circle cx="10" cy="10" r="9"/><circle cx="10" cy="8" r="3"/><path d="M4.5 16c1.5-2.5 3.5-3.5 5.5-3.5s4 1 5.5 3.5"/></svg>
    <span>Login &nbsp;/ Jion Us</span>
  </div>
</header>

<nav class="mainnav">
  <svg class="abs" style="left:112px;top:19px" width="30" height="22" viewBox="0 0 30 22"><path d="M0 2h30M0 11h30M0 20h30" stroke="#222" stroke-width="2.4"/></svg>
  <span class="abs link active" style="left:334px">SHOP</span>
  <span class="abs link" style="left:448px">REVIEWS</span>
  <span class="abs link" style="left:563px">BLOG</span>
  <span class="abs link" style="left:688px">OUR STORY</span>
  <span class="abs link" style="left:839px">WHOLESALE</span>
  <svg class="abs icon" style="left:1000px;top:20px;color:#444" width="22" height="20" viewBox="0 0 22 20"><path d="M1 2h3l2.5 10h10l2-7H6"/><circle cx="8" cy="16" r="1.5"/><circle cx="15" cy="16" r="1.5"/></svg>
  <span class="abs" style="left:1012px;top:14px;width:10px;height:10px;border-radius:50%;background:var(--pink);color:#fff;font-size:7px;text-align:center;line-height:10px">0</span>
  <svg class="abs icon" style="left:1031px;top:21px;color:#444" width="20" height="18" viewBox="0 0 20 18"><path d="M10 16S2 11 2 6a4 4 0 0 1 8-1 4 4 0 0 1 8 1c0 5-8 10-8 10z"/></svg>
  <svg class="abs icon" style="left:1062px;top:18px;color:#444" width="24" height="24" viewBox="0 0 24 24"><circle cx="10" cy="10" r="7.5"/><path d="M15.5 15.5L22 22"/></svg>
</nav>

<section class="hero" role="img" aria-label="Galaxy nebula with hemp leaves in blue and violet tones">
  <h1 class="abs">STARLEAF</h1>
  <p class="abs">Lorem ipsum dolor sit amet, consectetur adipiscing elit, sed do eiusmod<br>tempor incididunt ut labore et dolore magna aliqua.</p>
  <div class="abs btn-ghost" style="left:507px;top:353px;width:186px;height:48px">BROWSE PRODUCT</div>
  <svg class="abs icon" style="left:76px;top:288px;color:#fff" width="16" height="30" viewBox="0 0 16 30"><path d="M14 2L2 15l12 13"/></svg>
  <svg class="abs icon" style="left:1116px;top:288px;color:#fff" width="16" height="30" viewBox="0 0 16 30"><path d="M2 2l12 13L2 28"/></svg>
  <div class="abs dots" style="left:564px;top:564px"><span class="on"></span><span></span><span></span><span></span></div>
</section>

<section class="products">
  <h2 class="abs serif-title" style="top:74px;width:100%">Featured Products</h2>
  <p class="abs lead" style="top:132px;width:100%">Lorem ipsum dolor sit amet, consectetur adipiscing elit</p>

  <div class="abs card" style="left:112px">
    <div class="shot"><div class="pouch" role="img" aria-label="Green product pouch" style="background:linear-gradient(180deg,#cfd4cf 0 12%,#2f8a3a 12% 100%)"></div></div>
    <div class="btn-cart">ADD TO CART</div><div class="name">Product Name</div><div class="price">$123</div>
  </div>
  <div class="abs card" style="left:360px">
    <div class="shot"><div class="pouch" role="img" aria-label="Silver product pouch" style="background:linear-gradient(90deg,#9a9a9a,#e8e8e8 50%,#8f8f8f)"></div></div>
    <div class="btn-cart">ADD TO CART</div><div class="name">Product Name</div><div class="price">$123</div>
  </div>
  <div class="abs card" style="left:608px">
    <div class="shot"><div class="pouch" role="img" aria-label="Silver pouch with colourful accessories" style="background:linear-gradient(90deg,#a0a0a0,#eaeaea 50%,#9a9a9a)"></div></div>
    <div class="btn-cart">ADD TO CART</div><div class="name">Product Name</div><div class="price">$123</div>
  </div>
  <div class="abs card" style="left:856px">
    <div class="shot"><div class="pouch" role="img" aria-label="Black product pouch" style="background:linear-gradient(180deg,#bbb 0 12%,#1c1c1c 12% 100%)"></div></div>
    <div class="btn-cart">ADD TO CART</div><div class="name">Product Name</div><div class="price">$123</div>
  </div>

  <svg class="abs icon" style="left:112px;top:579px;color:#333" width="24" height="18" viewBox="0 0 24 18"><path d="M23 9H2M9 2L2 9l7 7"/></svg>
  <div class="abs dots pager" style="left:578px;top:583px"><span class="on"></span><span></span><span></span></div>
  <svg class="abs icon" style="left:1064px;top:579px;color:#333" width="24" height="18" viewBox="0 0 24 18"><path d="M1 9h21M15 2l7 7-7 7"/></svg>
</section>

<section class="categories">
  <h2 class="abs serif-title" style="top:20px;width:100%">Shop by Categories</h2>
  <div class="abs cat" style="left:23px;background:linear-gradient(160deg,#6a7b2c,#3a4a18 50%,#2a2618)" role="img" aria-label="Close-up of a flowering hemp plant">
    <div class="label">FLOWERS</div><div class="shop">SHOP NOW</div>
  </div>
  <div class="abs cat" style="left:414px;background:linear-gradient(160deg,#4a4e4e,#7a7a78 40%,#3a3330)" role="img" aria-label="Person smoking a pre-roll in soft smoke">
    <div class="label">PRE-ROLLS</div><div class="shop">SHOP NOW</div>
  </div>
  <div class="abs cat" style="left:805px;background:linear-gradient(160deg,#8aa064,#b89078 45%,#5a4f52)" role="img" aria-label="Woman outdoors holding a vape device">
    <div class="label">VAPES</div><div class="shop">SHOP NOW</div>
  </div>
</section>

<section class="story" role="img" aria-label="Hemp bud and leaves against a dark background">
  <h2 class="abs">Beyond the High</h2>
  <p class="abs">Lorem ipsum dolor sit amet, consectetur adipiscing elit, sed do eiusmod tempor incididunt ut labore et dolore magna aliqua. Quis ipsum suspendisse ultrices gravida. Risus commodo viverra maecenas accumsan lacus vel facilisis.</p>
</section>

<section class="blog">
  <h2 class="abs serif-title" style="top:70px;width:100%">Featured Blog</h2>
  <p class="abs lead" style="top:128px;width:100%">Lorem ipsum dolor sit amet, consectetur adipiscing elit</p>

  <article class="abs post" style="left:112px">
    <div class="shot" role="img" aria-label="Sunrise over a hemp field" style="background:linear-gradient(180deg,#d9a23a,#7a7a2a 35%,#2e4a1e 70%,#1e3214)"></div>
    <div class="meta"><span>&#9632; Thu Jun 20</span><span>&#9679; Admin</span><span>&#9675; (22)</span></div>
    <h3>Lorem ipsum dolor sit amet,</h3>
    <p>Lorem ipsum dolor sit amet, consecte adipiscing elit, sed do eiusmod tempor incididunt ut labore et dolore magna aliqua.</p>
    <div class="more">CONTINUE READING &raquo;</div>
  </article>
  <article class="abs post" style="left:444px">
    <div class="shot" role="img" aria-label="Oil bottle beside dried hemp buds" style="background:linear-gradient(160deg,#3a5a2a,#7a6a3a 45%,#4a3a28)"></div>
    <div class="meta"><span>&#9632; Thu Jun 20</span><span>&#9679; Admin</span><span>&#9675; (22)</span></div>
    <h3>Lorem ipsum dolor sit amet,</h3>
    <p>Lorem ipsum dolor sit amet, consecte adipiscing elit, sed do eiusmod tempor incididunt ut labore et dolore magna aliqua.</p>
    <div class="more">CONTINUE READING &raquo;</div>
  </article>
  <article class="abs post" style="left:776px">
    <div class="shot" role="img" aria-label="Person seated in a chair by a white wall" style="background:linear-gradient(160deg,#e8e8e8,#c8c8c8 50%,#4a4a4a)"></div>
    <div class="meta"><span>&#9632; Thu Jun 20</span><span>&#9679; Admin</span><span>&#9675; (22)</span></div>
    <h3>Lorem ipsum dolor sit amet,</h3>
    <p>Lorem ipsum dolor sit amet, consecte adipiscing elit, sed do eiusmod tempor incididunt ut labore et dolore magna aliqua.</p>
    <div class="more">CONTINUE READING &raquo;</div>
  </article>
</section>

<section class="newsletter" role="img" aria-label="Starry night sky over a dark forest">
  <h2 class="abs serif-title">Subscribe to our Newsletter</h2>
  <p class="abs sub">A short sentence describing what someone will receive by subscribing</p>
  <div class="abs field">Your email</div>
  <div class="abs send"><svg width="24" height="24" viewBox="0 0 24 24"><path d="M22 2L2 10l7 3 3 8z" fill="#fff"/></svg></div>
</section>

<footer class="footer">
  <div class="abs brand" style="left:112px;top:62px;font-size:26px"><span class="dot"></span>STARLEAF</div>
  <div class="abs" style="left:112px;top:134px;display:flex;gap:8px">
    <span class="social" aria-label="Social profile"></span><span class="social" aria-label="Social profile"></span><span class="social" aria-label="Social profile"></span>
  </div>
  <div class="abs" style="left:421px;top:72px">
    <h4>NAVIGATION</h4>
    <ul><li>Shop</li><li>Reviews</li><li>Blog</li><li>Our Story</li><li>Wholesale</li></ul>
  </div>
  <div class="abs" style="left:651px;top:72px">
    <h4>CONTACT US</h4>
    <ul>
      <li><svg width="10" height="13" viewBox="0 0 10 13"><path d="M5 0a5 5 0 0 0-5 5c0 3.5 5 8 5 8s5-4.5 5-8a5 5 0 0 0-5-5z" fill="#fff"/></svg>123 Avenue name, City name</li>
      <li style="padding-left:18px">10150, United States</li>
      <li><svg width="12" height="12" viewBox="0 0 12 12"><path d="M2 0l3 3-1.5 2a7 7 0 0 0 3.5 3.5L9 7l3 3-2 2C5 12 0 7 0 2z" fill="#fff"/></svg>1-xxx-xxx-xxxx</li>
      <li><svg width="12" height="12" viewBox="0 0 12 12"><rect x="1" y="4" width="10" height="7" fill="#fff"/><rect x="3" y="0" width="6" height="4" fill="#fff"/></svg>1-xxx-xxx-xxxx</li>
      <li><svg width="12" height="10" viewBox="0 0 12 10"><rect width="12" height="10" fill="#fff"/><path d="M0 0l6 5 6-5" stroke="#0a0a1c" fill="none"/></svg>info@starleafshop.com</li>
    </ul>
  </div>
  <div class="abs" style="left:933px;top:72px">
    <h4>RESOURCES</h4>
    <ul><li>Blog</li><li>Newsletter</li><li>FAQs</li><li>Compensation Disclosure</li></ul>
  </div>
  <div class="abs" style="left:106px;top:247px;width:988px;height:1px;background:#3a3a55"></div>
  <p class="abs copyright">Copyright © 2020 &nbsp;Starleaf , All Rights Reserved.</p>
</footer>

</body>
</html>
```